Larkspur Talent IT Recruiting firm needs a business card design for Recruiters, Sourcers, and Account

We need business cards that allow us to change all contact info, names, titles (Recruiter, Sourcer, Account Manager, Director, CEO, etc) per person since we have three offices, in three cities, Phoenix, Austin, and Las Vegas. We do recruiting and contractors for IT positions (Developers, Architects, Software Engineers, Security Engineers, Help Desk, DBAs, PMs, Scrum Masters, etc.) Our client companies are very diverse from Meridian 100 to silicone Valley type start-ups.

So, while we what hip, techie, and quirky, it still needs to be professional. Primary color we use is blue, with silver as a secondary color.

Target Market(s)

IT, Technology

Industry/Entity Type

Business

Contact Information for Business Card

Company name: Larkspur Talent, Inc.
Website: www.larkspurtalent.example
Logos for Careerloop, Blipster, and Myriada

Name, Title, Office Number, Cell Number, email

Font styles to use
Serif
Sans Serif

Colors
0455a3
d5d5d5

Requirements
Nice to have
• The grey I selected below is not necessary - but, would like silver included. I included a card design (File 3: LTI early trial example.jpg) that I had started on. It's very rough, and not quite what we're looking for, but what we did like is the logo, big, maybe a bit faded, off center, goes out of frame, etc. Still looking for other ideas - you are the pros! But, just an idea of a design element we liked.

```html
<!DOCTYPE html>
<html lang="en">
<head>
<meta charset="utf-8">
<title>Larkspur Talent — Business Cards</title>
<link rel="stylesheet" href="https://fonts.googleapis.com/css2?family=Lato:wght@400;700&family=Marcellus&display=swap">
<style>
  :root {
    --page-bg: #e9e9ea;
    --card-bg: #1d1e20;
    --card-bg-edge: #141516;
    --brand-blue: #0455a3;
    --sky-blue: #3fb6f6;
    --link-blue: #2e9fe6;
    --silver: #d5d5d5;
    --muted-silver: #9a9a9c;
    --chip-bg: #2c2d30;
  }
  * { box-sizing: border-box; margin: 0; padding: 0; }
  html, body {
    width: 1200px; height: 900px; overflow: hidden;
    background: var(--page-bg);
    font-family: "Lato", Arial, sans-serif;
  }
  .canvas { position: relative; width: 1200px; height: 900px; }

  .card {
    position: absolute;
    width: 620px; height: 354px;
    overflow: hidden;
    border-radius: 4px;
    background: radial-gradient(ellipse at 45% 40%, var(--card-bg) 0%, var(--card-bg-edge) 100%);
    box-shadow: 0 10px 28px rgba(0,0,0,0.22);
  }
  .card--back  { left: 90px;  top: 70px; }
  .card--front { left: 490px; top: 476px; }

  .card__art { position: absolute; top: 0; }
  .card--back .card__art  { left: 0; }
  .card--front .card__art { right: 0; }

  .wordmark {
    position: absolute;
    display: flex; align-items: center; gap: 10px;
    font-family: "Marcellus", Georgia, serif;
    font-size: 34px; letter-spacing: 2px;
    color: var(--silver);
    white-space: nowrap;
  }
  .wordmark__dot {
    width: 30px; height: 30px; border-radius: 50%;
    background: var(--brand-blue);
  }
  .tagline {
    position: absolute;
    font-family: "Marcellus", Georgia, serif;
    font-size: 13px; letter-spacing: 3.5px;
    color: var(--muted-silver);
    white-space: nowrap;
  }
  .card--back .wordmark { left: 222px; top: 68px; }
  .card--back .tagline  { left: 262px; top: 122px; }

  .website {
    position: absolute; left: 300px; top: 186px;
    font-size: 17px; color: var(--link-blue);
  }
  .social {
    position: absolute; left: 300px; top: 226px;
    display: flex; gap: 12px; list-style: none;
  }
  .social__item {
    display: flex; align-items: center; gap: 5px;
    font-size: 11px; color: var(--muted-silver);
  }
  .social__dot {
    width: 12px; height: 12px; border-radius: 50%;
    background: var(--chip-bg);
  }

  .card--front .wordmark { left: 62px;  top: 58px; }
  .card--front .tagline  { left: 104px; top: 112px; }

  .person { position: absolute; right: 262px; top: 170px; text-align: right; }
  .person__name  { font-size: 21px; font-weight: 700; color: #ffffff; }
  .person__title { font-size: 16px; color: var(--link-blue); margin-top: 2px; }

  .contacts {
    position: absolute; right: 262px; top: 236px;
    list-style: none; text-align: right;
  }
  .contacts__item {
    display: flex; justify-content: flex-end; align-items: center; gap: 6px;
    font-size: 17px; color: var(--silver); line-height: 25px;
  }
  .contacts__icon { width: 12px; height: 12px; fill: var(--sky-blue); }
</style>
</head>
<body>
<main class="canvas">

  <section class="card card--back" aria-label="Business card back">
    <svg class="card__art" width="240" height="354" viewBox="0 0 240 354" role="img" aria-label="Large brand emblem decoration bleeding off the left edge">
      <defs>
        <linearGradient id="emblemFadeBack" x1="0" y1="0" x2="0" y2="1">
          <stop offset="0" stop-color="var(--sky-blue)"/>
          <stop offset="1" stop-color="var(--brand-blue)"/>
        </linearGradient>
      </defs>
      <circle cx="30" cy="160" r="200" fill="url(#emblemFadeBack)"/>
    </svg>

    <div class="wordmark"><span class="wordmark__dot"></span>LARKSPUR TALENT</div>
    <p class="tagline">RISING TO THE CHALLENGE</p>
    <p class="website">www.larkspurtalent.example</p>
    <ul class="social">
      <li class="social__item"><span class="social__dot"></span>Myriada</li>
      <li class="social__item"><span class="social__dot"></span>Blipster</li>
      <li class="social__item"><span class="social__dot"></span>Careerloop</li>
    </ul>
  </section>

  <section class="card card--front" aria-label="Business card front">
    <svg class="card__art" width="240" height="354" viewBox="0 0 240 354" role="img" aria-label="Large brand emblem decoration bleeding off the right edge">
      <defs>
        <linearGradient id="emblemFadeFront" x1="0" y1="0" x2="0" y2="1">
          <stop offset="0" stop-color="var(--sky-blue)"/>
          <stop offset="1" stop-color="var(--brand-blue)"/>
        </linearGradient>
      </defs>
      <circle cx="210" cy="120" r="170" fill="url(#emblemFadeFront)"/>
    </svg>

    <div class="wordmark"><span class="wordmark__dot"></span>LARKSPUR TALENT</div>
    <p class="tagline">RISING TO THE CHALLENGE</p>

    <div class="person">
      <p class="person__name">Dana Whitfield R</p>
      <p class="person__title">Designation</p>
    </div>

    <ul class="contacts">
      <li class="contacts__item">555 014-2290
        <svg class="contacts__icon" viewBox="0 0 12 12" aria-hidden="true"><path d="M1 4c0-2 2-3 5-3s5 1 5 3l-2 1-1-2H4L3 5zM3 6h6l1 5H2z"/></svg>
      </li>
      <li class="contacts__item">555 014-2290
        <svg class="contacts__icon" viewBox="0 0 12 12" aria-hidden="true"><path d="M3 0h6v12H3zM4 1v8h4V1z"/></svg>
      </li>
      <li class="contacts__item">info@larkspurtalent.example
        <svg class="contacts__icon" viewBox="0 0 12 12" aria-hidden="true"><path d="M0 2h12v8H0zM1 3l5 4 5-4z"/></svg>
      </li>
    </ul>
  </section>

</main>
</body>
</html>
```